Bus Stop sign for cafe (retro caravan)

outdoor bus stop sign for EL TRAPICHE, produced in Aluminium Composite Panel (ACP).
Material & use
Material: ACP (outdoor suitable)
Installation: Outdoor bus stop (public area) – please recommend the best finish for weather + UV + potential vandalism exposure (e.g., anti-graffiti laminate).
Size (as measured)
My measurements are:
Side A: 2.60 m
Side B: 1.245 m
Side C: 1.725 m
Side D: 1.200 m
I would love a creative and efficient design, keep simple, effective but creative at the same time, maybe son retro vintage style.
The sign should include logo, photo of the caravan and basic information, that way clients can find El Trapiche.
the information is:
Coffee • Breakfast • Brunch
Open daily 7:00–12:30 | Closed Wednesdays
Keep the info block clean and minimal:
118 Wattlebird Rd, Agnes Water
@eltrapiche_cafe
If you want to research more about my business visit my instagram @eltrapiche_cafe or website www.eltrapiche-example.com.au
Target Market(s)
tourist, locals,
Look and feel

```html
<!DOCTYPE html>
<html lang="en">
<head>
<meta charset="utf-8">
<title>El Trapiche – Bus Stop Sign</title>
<link rel="stylesheet" href="https://fonts.googleapis.com/css2?family=Yanone+Kaffeesatz:wght@400;500;600&display=swap">
<style>
  :root {
    --page-bg: #e8e5e0;
    --cream: #f9ede2;
    --brown: #ad5a2f;
    --orange: #f7954a;
    --light-orange: #fbb76b;
    --ink: #2b2320;
    --photo-sky: #c9d8e2;
    --photo-leaf: #6f7f55;
    --photo-van: #e8e0d4;
    --photo-grass: #3f8a45;
  }
  html, body {
    margin: 0;
    width: 1200px;
    height: 1200px;
    overflow: hidden;
    background: var(--page-bg);
  }
  .canvas {
    width: 1200px;
    height: 1200px;
    display: flex;
    align-items: center;
    justify-content: center;
  }
  .sign {
    width: 664px;
    height: 1140px;
    display: block;
    filter: drop-shadow(0 6px 14px rgba(0,0,0,0.18));
  }
  .sign text { font-family: "Yanone Kaffeesatz", sans-serif; }
  .badge-name { font-weight: 600; font-size: 40px; fill: var(--ink); }
  .hero-name { font-weight: 600; font-size: 104px; fill: var(--cream); }
  .services { font-weight: 600; font-size: 72px; fill: var(--ink); }
  .hours { font-weight: 500; font-size: 84px; fill: var(--ink); }
  .contact { font-weight: 400; font-size: 52px; fill: var(--ink); }
</style>
</head>
<body>
<main class="canvas">
  <svg class="sign" viewBox="0 0 772 1325" xmlns="http://www.w3.org/2000/svg" aria-label="El Trapiche bus stop sign">
    <defs>
      <clipPath id="sign-shape">
        <polygon points="0,0 772,210 772,1325 0,1325"/>
      </clipPath>
      <linearGradient id="photo-tone" x1="0" y1="0" x2="0" y2="1">
        <stop offset="0" stop-color="var(--photo-sky)"/>
        <stop offset="0.25" stop-color="var(--photo-leaf)"/>
        <stop offset="0.45" stop-color="var(--photo-van)"/>
        <stop offset="0.7" stop-color="#c76a35"/>
        <stop offset="1" stop-color="var(--photo-grass)"/>
      </linearGradient>
      <path id="band-line" d="M-40,745 C200,900 560,880 820,540"/>
      <path id="services-line" d="M-40,770 C200,925 560,905 820,565"/>
    </defs>

    <g clip-path="url(#sign-shape)">
      <rect class="sign-base" x="0" y="0" width="772" height="1325" fill="var(--cream)"/>

      <rect class="caravan-photo" x="0" y="0" width="772" height="700" fill="url(#photo-tone)"
            role="img" aria-label="Photo of the retro orange and white caravan cafe on green turf"/>

      <!-- right brown sweep -->
      <path class="sweep-brown" d="M820,540 L820,1345 L400,1345 C660,1210 735,980 660,760 Z" fill="var(--brown)"/>
      <path class="sweep-stripe-orange" d="M410,1345 C660,1210 735,980 660,760" fill="none" stroke="var(--orange)" stroke-width="70"/>
      <path class="sweep-stripe-light" d="M410,1345 C660,1210 735,980 660,760" fill="none" stroke="var(--light-orange)" stroke-width="34"/>

      <!-- info panel -->
      <path class="info-panel" d="M-10,770 L645,770 C715,980 640,1210 380,1345 L-10,1345 Z" fill="var(--cream)"/>

      <!-- brand oval -->
      <ellipse class="brand-oval" cx="300" cy="650" rx="330" ry="135" fill="var(--brown)"/>
      <text class="hero-name" x="300" y="690" text-anchor="middle">El Trapiche</text>

      <!-- services band -->
      <use href="#band-line" fill="none" stroke="var(--cream)" stroke-width="140"/>
      <use href="#band-line" fill="none" stroke="var(--light-orange)" stroke-width="122"/>
      <use class="services-band" href="#band-line" fill="none" stroke="var(--orange)" stroke-width="100"/>
      <text class="services"><textPath href="#services-line" startOffset="60">Coffee • Breakfast • Brunch</textPath></text>

      <!-- badge -->
      <circle class="badge" cx="115" cy="147" r="90" fill="#ffffff" stroke="var(--orange)" stroke-width="12"/>
      <text class="badge-name" x="115" y="160" text-anchor="middle">El Trapiche</text>

      <!-- info block -->
      <text class="hours" x="44" y="1000">Open daily 7:00–12:30</text>
      <text class="hours" x="44" y="1085">Closed Wednesdays</text>
      <line class="info-rule" x1="38" y1="1120" x2="632" y2="1120" stroke="var(--ink)" stroke-width="4"/>
      <text class="contact" x="46" y="1182">118 Wattlebird Rd, Agnes Water</text>
      <text class="contact" x="46" y="1240" textLength="450" lengthAdjust="spacingAndGlyphs">www.eltrapiche-example.com.au</text>
      <text class="contact" x="46" y="1300">@eltrapiche_cafe</text>
    </g>
  </svg>
</main>
</body>
</html>
```